Plumo Ridge - Graphic Label

Company Name: Verdant Loom
Product: Organic Energy Drink
Name of Drink : Plumo Ridge
8.45oz - Bottle
http://www.trellimart.example/item/metal-beverage-flask_2749301856.html?s=p
Attached will be examples of labels for other drinks associated with this company along with company logo. I'm open to all interpretations of design. Please submit creative ideas and we can adjust design as we go.
Design must have some integration of the geometry as seen in labels attached.
Keep it classy
If you have a vision for the design, just create it and we can adjust from there.
I want the bottle to have long lasting but creative/interesting design..
Reason: Design sought has not been submited, the deadline has been extended.
Please continue submissions.
- Thanks
Target Market(s)
All Ages .. those interested in Organics, health drinks, energy drinks
Industry/Entity Type
It Company
Look and feel

```html
<!DOCTYPE html>
<html lang="en">
<head>
<meta charset="utf-8">
<title>Plumo Ridge – Organic Energy Label</title>
<link rel="stylesheet" href="https://fonts.googleapis.com/css2?family=Baloo+2:wght@700;800&family=Roboto+Condensed:wght@400;700&family=Kaushan+Script&family=Roboto+Slab:wght@400;700&display=swap">
<style>
  :root {
    --page: #ffffff;
    --silver-light: #f4f5f6;
    --silver-mid: #d9dcdf;
    --silver-dark: #b4b8bd;
    --hex-tone: #e3e6e8;
    --purple: #5a2a8e;
    --purple-deep: #3f1a6b;
    --purple-light: #7a44b0;
    --leaf: #6fbf4a;
    --leaf-pale: #b9dfa3;
    --berry: #2b1530;
    --white: #ffffff;
  }
  * { box-sizing: border-box; margin: 0; padding: 0; }
  html, body {
    width: 1012px; height: 1200px; overflow: hidden;
    background: var(--page);
  }
  .label {
    position: absolute; left: 156px; top: 170px;
    width: 700px; height: 860px;
    border-radius: 6px;
    overflow: hidden;
  }
  .label__metal {
    position: absolute; left: 0; right: 0;
    background:
      radial-gradient(ellipse at 50% 50%, var(--hex-tone) 0%, transparent 70%),
      linear-gradient(90deg, var(--silver-dark) 0%, var(--silver-light) 30%, var(--silver-mid) 60%, var(--silver-light) 80%, var(--silver-dark) 100%);
  }
  .label__metal--top { top: 0; height: 118px; }
  .label__metal--bottom { top: 678px; height: 182px; }
  .label__maker {
    position: absolute; top: 40px; left: 0; right: 0;
    display: flex; justify-content: center; align-items: center; gap: 10px;
    font-family: "Roboto Condensed", sans-serif; font-weight: 700; font-size: 22px;
    color: var(--leaf); letter-spacing: 2px;
  }
  .label__maker-dot { width: 14px; height: 14px; border-radius: 50%; background: var(--leaf); }
  .label__stripe {
    position: absolute; left: 0; right: 0; height: 14px;
    background: linear-gradient(90deg, var(--leaf-pale), #dff0d4, var(--leaf-pale));
  }
  .label__stripe--top { top: 118px; }
  .label__stripe--bottom { top: 664px; }
  .label__panel {
    position: absolute; top: 132px; left: 0; right: 0; height: 532px;
    background: linear-gradient(90deg, var(--purple-deep) 0%, var(--purple) 25%, var(--purple-light) 55%, var(--purple) 80%, var(--purple-deep) 100%);
    text-align: center; color: var(--white);
  }
  .label__name {
    margin-top: 52px;
    font-family: "Baloo 2", sans-serif; font-weight: 800; font-size: 128px; line-height: 0.9;
    letter-spacing: 2px;
  }
  .label__subname {
    font-family: "Roboto Condensed", sans-serif; font-weight: 700; font-size: 52px;
    letter-spacing: 10px; margin-top: 6px;
  }
  .label__art {
    width: 300px; height: 170px; margin: 20px auto 0;
    border-radius: 40px;
    background: radial-gradient(ellipse at 50% 50%, var(--berry) 0%, #3d2050 45%, rgba(111,191,74,0.55) 80%, rgba(111,191,74,0) 100%);
  }
  .label__tagline {
    font-family: "Kaushan Script", cursive; font-size: 46px; margin-top: 14px;
  }
  .label__claims {
    position: absolute; top: 710px; left: 0; right: 0;
    display: flex; justify-content: center; gap: 26px;
  }
  .claim { position: relative; width: 118px; height: 104px; }
  .claim svg { position: absolute; inset: 0; }
  .claim__text {
    position: absolute; inset: 0; display: flex; flex-direction: column;
    justify-content: center; align-items: center;
    font-family: "Roboto Slab", serif; font-weight: 700; font-size: 19px; line-height: 1.15;
    color: var(--white);
  }
</style>
</head>
<body>
  <main class="label">
    <div class="label__metal label__metal--top" role="img" aria-label="Brushed silver band with faint hexagon pattern"></div>
    <div class="label__maker"><span class="label__maker-dot"></span>Verdant Loom</div>
    <div class="label__stripe label__stripe--top"></div>

    <section class="label__panel">
      <h1 class="label__name">Plumo</h1>
      <div class="label__subname">RIDGE</div>
      <div class="label__art" role="img" aria-label="Cluster of dark purple berries with green leaves"></div>
      <p class="label__tagline">Organic Energy</p>
    </section>

    <div class="label__stripe label__stripe--bottom"></div>
    <div class="label__metal label__metal--bottom" role="img" aria-label="Brushed silver band with faint hexagon pattern"></div>

    <div class="label__claims">
      <div class="claim">
        <svg viewBox="0 0 118 104"><polygon points="30,2 88,2 116,52 88,102 30,102 2,52" fill="#6fbf4a" stroke="#ffffff" stroke-width="3"/></svg>
        <div class="claim__text"><span>100%</span><span>Juice</span></div>
      </div>
      <div class="claim">
        <svg viewBox="0 0 118 104"><polygon points="30,2 88,2 116,52 88,102 30,102 2,52" fill="#6fbf4a" stroke="#ffffff" stroke-width="3"/></svg>
        <div class="claim__text"><span>No</span><span>GMO</span></div>
      </div>
      <div class="claim">
        <svg viewBox="0 0 118 104"><polygon points="30,2 88,2 116,52 88,102 30,102 2,52" fill="#6fbf4a" stroke="#ffffff" stroke-width="3"/></svg>
        <div class="claim__text"><span>100%</span><span>Vegan</span></div>
      </div>
    </div>
  </main>
</body>
</html>
```